Business Card Design

New business card design

Target Market(s)

Residential & Commercial Property Managers

Industry/Entity Type

Plumbing Services

Contact Information for Business Card

Name - Rowan Keddle, title - Director, Phone Number - 0431 286 517, email - rowan@tbk-plumbing.com.au, Company ABN - 73 215 904 386,

Font styles to use
Sans Serif

Colors
0054AA
0677BA
7BADD7
CADEEF
E8F1F8

```html
<!DOCTYPE html>
<html lang="en">
<head>
<meta charset="utf-8">
<title>TBK Plumbing Services – Business Card</title>
<link rel="stylesheet" href="https://fonts.googleapis.com/css2?family=Source+Sans+3:ital,wght@0,300;0,400;0,600;1,600&display=swap">
<style>
  :root {
    --page: #ffffff;
    --card: #cae9f8;
    --accent: #2da9e1;
    --accent-soft: #a0dcf3;
    --ink: #1f2329;
    --muted: #6d6466;
    --on-accent: #ffffff;
  }
  * { box-sizing: border-box; margin: 0; padding: 0; }
  html, body {
    width: 1000px; height: 1200px; overflow: hidden;
    background: var(--page);
    font-family: "Source Sans 3", "Segoe UI", sans-serif;
  }
  .sheet { position: relative; width: 1000px; height: 1200px; }
  .card {
    position: absolute; left: 146px; width: 707px; height: 405px;
    background: var(--card); overflow: hidden;
  }
  .card--front { top: 144px; }
  .card--back { top: 630px; }

  .wordmark {
    position: absolute; left: 0; right: 0; text-align: center;
    color: var(--ink); font-weight: 400;
  }
  .wordmark__name { display: block; line-height: 1; }
  .wordmark__tagline {
    display: block; text-transform: lowercase; padding-left: 0.9em;
  }
  .card--front .wordmark { top: 100px; }
  .card--front .wordmark__name { font-size: 118px; letter-spacing: 10px; }
  .card--front .wordmark__tagline { font-size: 22px; letter-spacing: 0.9em; margin-top: 28px; }
  .card--back .wordmark { top: 36px; }
  .card--back .wordmark__name { font-size: 90px; letter-spacing: 8px; }
  .card--back .wordmark__tagline { font-size: 17px; letter-spacing: 0.9em; margin-top: 22px; }

  .abn-band { position: absolute; left: 0; bottom: 0; width: 707px; height: 51px; }
  .abn {
    position: absolute; left: 0; right: 0; bottom: 12px; text-align: center;
    color: var(--on-accent); font-weight: 300; font-size: 21px;
  }

  .backdrop { position: absolute; left: 0; top: 0; width: 707px; height: 405px; }

  .contact {
    position: absolute; top: 224px; left: 0; right: 0; text-align: center; color: var(--ink);
  }
  .contact__name { font-size: 33px; font-weight: 600; letter-spacing: -0.3px; line-height: 1.1; }
  .contact__title { font-size: 23px; font-style: italic; font-weight: 600; margin-top: 4px; }
  .contact__line {
    display: flex; justify-content: center; align-items: center; gap: 8px;
    font-size: 21px; font-weight: 300; margin-top: 6px;
  }
  .contact__line svg { width: 17px; height: 17px; fill: var(--muted); }
  .contact__line--email { margin-top: 4px; }
</style>
</head>
<body>
<main class="sheet">
  <section class="card card--front">
    <div class="wordmark">
      <span class="wordmark__name">TBK</span>
      <span class="wordmark__tagline">plumbing services</span>
    </div>
    <svg class="abn-band" viewBox="0 0 707 51" aria-hidden="true">
      <path fill="var(--accent)" d="M0 35 H184 C200 35 210 30 220 18 C230 6 238 0 256 0 H450 C468 0 476 6 486 18 C496 30 506 35 522 35 H707 V51 H0 Z"/>
    </svg>
    <p class="abn">ABN - 73 215 904 386</p>
  </section>

  <section class="card card--back">
    <svg class="backdrop" viewBox="0 0 707 405" aria-hidden="true">
      <circle cx="-60" cy="300" r="240" fill="var(--accent-soft)"/>
    </svg>
    <div class="wordmark">
      <span class="wordmark__name">TBK</span>
      <span class="wordmark__tagline">plumbing services</span>
    </div>
    <div class="contact">
      <p class="contact__name">Rowan Keddle</p>
      <p class="contact__title">Director</p>
      <p class="contact__line">
        <svg viewBox="0 0 24 24" aria-hidden="true"><path d="M6.6 10.8a15.1 15.1 0 0 0 6.6 6.6l2.2-2.2c.3-.3.7-.4 1-.2 1.1.4 2.3.6 3.6.6.6 0 1 .4 1 1V20c0 .6-.4 1-1 1A17 17 0 0 1 3 4c0-.6.4-1 1-1h3.5c.6 0 1 .4 1 1 0 1.3.2 2.5.6 3.6.1.3 0 .7-.2 1z"/></svg>
        <span>0431 286 517</span>
      </p>
      <p class="contact__line contact__line--email">
        <svg viewBox="0 0 24 24" aria-hidden="true"><path d="M2 5h20v2l-10 6L2 7z M2 9l10 6 10-6v10H2z"/></svg>
        <span>rowan@tbk-plumbing.com.au</span>
      </p>
    </div>
  </section>
</main>
</body>
</html>
```